Northfield Builders Guild Business card

We are looking for a new business card design with photo included.
Our business is a nonprofit construction contractor membership organization. We offer business education, assist with business setup and licensing, provide safety training, and provide a member directory.
URL: www.builderslinkguild.org
Color code:
CMYK: 0 cyan, 42 magenta, 100 yellow, 0 black for Print.
Hexidecimal: #FF9900
RGB: R 255; G 153; B 0

```html
<!DOCTYPE html>
<html lang="en">
<head>
<meta charset="utf-8">
<title>Northfield Builders Guild – Business Card</title>
<link href="https://fonts.googleapis.com/css2?family=Source+Sans+3:wght@400;600;700&display=swap" rel="stylesheet">
<style>
  :root {
    --bg: #cfcfcf;
    --charcoal: #3a393a;
    --ink: #2f2f30;
    --paper: #ffffff;
    --orange: #f0a020;
    --muted: #e6e6e6;
  }
  * { box-sizing: border-box; margin: 0; padding: 0; }
  html, body { width: 1200px; height: 800px; overflow: hidden; }
  body {
    background: var(--bg);
    font-family: "Source Sans 3", sans-serif;
    position: relative;
  }
  .card {
    position: absolute;
    width: 525px;
    height: 300px;
    box-shadow: 0 6px 18px rgba(0,0,0,0.18);
    overflow: hidden;
  }
  /* Back of card */
  .card-back {
    left: 55px; top: 120px;
    background: var(--charcoal);
    color: var(--paper);
    display: flex; flex-direction: column; align-items: center; justify-content: center;
    text-align: center;
  }
  .brand-name {
    font-weight: 700;
    text-transform: uppercase;
    line-height: 0.95;
    letter-spacing: 0.5px;
  }
  .card-back .brand-name { font-size: 42px; color: var(--paper); }
  .divider-short {
    width: 50px; height: 2px; background: var(--orange); margin: 22px 0 20px;
  }
  .services {
    font-size: 13px; letter-spacing: 0.6px; text-transform: uppercase; line-height: 1.55;
    color: var(--muted);
  }
  .services .dot { color: var(--orange); padding: 0 4px; }

  /* Front of card */
  .card-front {
    left: 620px; top: 380px;
    background: var(--paper);
    color: var(--ink);
  }
  .edge-band {
    position: absolute; left: 0; top: 0; width: 14px; height: 100%;
    background: linear-gradient(to bottom, var(--charcoal) 0 58%, var(--orange) 58% 100%);
  }
  .card-front .brand-name {
    position: absolute; right: 34px; top: 34px;
    font-size: 26px; color: var(--ink); text-align: right;
  }
  .rule {
    position: absolute; left: 46px; right: 30px; top: 128px; height: 2px; background: var(--orange);
  }
  .person { position: absolute; left: 46px; top: 84px; }
  .person-name { font-size: 22px; font-weight: 600; color: var(--orange); line-height: 1; }
  .person-title { font-size: 15px; color: var(--ink); margin-top: 4px; }
  .contact { position: absolute; left: 46px; top: 140px; font-size: 14px; line-height: 1.45; }
  .contact-address { margin-bottom: 2px; }
  .contact-row { display: flex; align-items: center; gap: 7px; }
  .contact-row svg { width: 12px; height: 12px; flex: none; }
</style>
</head>
<body>

<section class="card card-back" aria-label="Business card back">
  <div class="brand-name">Northfield<br>Builders Guild</div>
  <div class="divider-short"></div>
  <p class="services">Technical Assistance<span class="dot">•</span>Contractor Education<br>Safety &amp; Compliance<span class="dot">•</span>Contractor Directory</p>
</section>

<section class="card card-front" aria-label="Business card front">
  <div class="edge-band"></div>
  <div class="brand-name">Northfield<br>Builders Guild</div>
  <div class="person">
    <div class="person-name">Daniel Whitaker</div>
    <div class="person-title">President</div>
  </div>
  <div class="rule"></div>
  <div class="contact">
    <div class="contact-address">4820 Cedar Ridge Rd., Suite #210<br>Millbrook, OR 97301</div>
    <div class="contact-row">
      <svg viewBox="0 0 12 12" aria-hidden="true"><path d="M3 1 L5 3.5 L4 5 Q5 7 7 8 L8.5 7 L11 9 L9.5 11 Q4 10.5 1 3 Z" fill="#f0a020"/></svg>
      (555) 318-2047
    </div>
    <div class="contact-row">
      <svg viewBox="0 0 12 12" aria-hidden="true"><rect x="3" y="1" width="6" height="4" fill="none" stroke="#f0a020" stroke-width="1.2"/><rect x="1" y="5" width="10" height="6" rx="1" fill="#f0a020"/></svg>
      555.274.0193
    </div>
    <div class="contact-row">
      <svg viewBox="0 0 12 12" aria-hidden="true"><rect x="1" y="2.5" width="10" height="7" fill="none" stroke="#f0a020" stroke-width="1.2"/><path d="M1 2.5 L6 7 L11 2.5" fill="none" stroke="#f0a020" stroke-width="1.2"/></svg>
      daniel@builderslinkguild.org
    </div>
    <div class="contact-row">
      <svg viewBox="0 0 12 12" aria-hidden="true"><circle cx="6" cy="6" r="5" fill="none" stroke="#f0a020" stroke-width="1.2"/><ellipse cx="6" cy="6" rx="2.2" ry="5" fill="none" stroke="#f0a020" stroke-width="1"/><path d="M1 6 H11" stroke="#f0a020" stroke-width="1"/></svg>
      www.builderslinkguild.org
    </div>
  </div>
</section>

</body>
</html>
```